Landingpage design

We need a landingpage for a Chatterloom add campaign. We sell socks made of bamboo in super quality. Our customers loves us, and we have a 5 heart rating at scorevane.com.

We want to create a add campaign targeted new customers, and the offer is that they can buy 1 pair of bamboo socks as a test, for only 20 DKK (2,7 Euro) including shipment. Our webpage is www.tuvelo.dk, landingpage should be built i Kyvio, a wysiwyg editor. based on their template. like:
https://tuvelo.pemlorsite.com/13844-sales-page
https://tuvelo.pemlorsite.com/13696-sales-page
https://tuvelo.pemlorsite.com/13845-sales-page

You don't have to follow the templates 100% if you have better ideas. We have an account for snapvaultly, so please get stockphotos from here.

Bamboo socks has a lot of great selling points, you can see a good desciption here:
https://feltrano.com/us/why-bamboo

We expect you to have experience in landingpage design, and expect to end up with 2 landingpages we can splittest on.

This is the first of a number of landingpages we need in the future, so for the right person there will be plenty of more work.

Target Market(s)

Denmark

Industry/Entity Type

E-Commerce

Number of Pages Required

2 page

Colors

Designer to choose colors to be used in the design.

Requirements
Must have
• A great selling page, showing all the great things with bamboo socks. It should be supplied with good packshots from snapvaultly.com

```html
<!DOCTYPE html>
<html lang="en">
<head>
<meta charset="utf-8">
<title>Tuvelo – Bamboo Socks</title>
<link rel="stylesheet" href="https://fonts.googleapis.com/css2?family=Roboto:wght@400;500;700&display=swap">
<style>
  :root {
    --green: #37b088;
    --green-dark: #2e9e79;
    --ink: #4a4a4a;
    --muted: #8c8c8c;
    --light-bg: #f2f2f2;
    --white: #ffffff;
    --cta-bg: #e9f3e7;
    --teal-line: #7ed3d6;
  }
  * { box-sizing: border-box; margin: 0; padding: 0; }
  html, body { width: 1200px; height: 2341px; overflow: hidden; }
  body { font-family: "Roboto", Arial, sans-serif; color: var(--ink); background: var(--white); position: relative; }

  .site-header { position: absolute; top: 0; left: 0; width: 1200px; height: 70px; background: var(--white); }
  .brand { position: absolute; left: 134px; top: 17px; display: flex; align-items: center; gap: 10px; }
  .brand-mark { width: 38px; height: 38px; border: 2px solid #222; }
  .brand-name { font-size: 17px; font-weight: 500; color: #222; line-height: 1.15; }
  .main-nav { position: absolute; top: 27px; left: 484px; font-size: 13px; text-transform: uppercase; color: #777; }
  .main-nav a { position: absolute; white-space: nowrap; text-decoration: none; color: inherit; }
  .main-nav a.active { color: #333; border-bottom: 1px solid #333; padding-bottom: 3px; }
  .btn { display: flex; align-items: center; justify-content: center; font-size: 13px; font-weight: 500; text-transform: uppercase; color: var(--white); background: var(--green); text-decoration: none; letter-spacing: .3px; }
  .header-cta { position: absolute; left: 908px; top: 20px; width: 158px; height: 29px; }

  .hero { position: absolute; top: 70px; left: 0; width: 1200px; height: 492px; }
  .hero-photo { position: absolute; inset: 0; background: linear-gradient(100deg, #6b6560 0%, #8a837c 35%, #c9bfb4 60%, #b39c89 100%); }
  .hero-shade { position: absolute; inset: 0; background: linear-gradient(90deg, rgba(40,40,40,.55) 0%, rgba(40,40,40,.25) 55%, rgba(40,40,40,0) 80%); }
  .hero-content { position: absolute; left: 134px; top: 103px; color: var(--white); }
  .hero-title { font-size: 41px; font-weight: 500; line-height: 1.2; width: 680px; }
  .hero-points { list-style: none; margin-top: 22px; font-size: 16px; }
  .hero-points li { display: flex; align-items: center; gap: 12px; height: 28px; }
  .hero-actions { display: flex; gap: 17px; margin-top: 20px; }
  .hero-actions .btn { width: 194px; height: 36px; }
  .btn-outline { background: transparent; border: 1.5px solid rgba(255,255,255,.85); gap: 10px; }
  .hero-note { font-size: 12px; margin-top: 10px; }

  .why { position: absolute; top: 562px; left: 0; width: 1200px; height: 587px; background: var(--light-bg); text-align: center; }
  .why-title { margin-top: 100px; font-size: 34px; font-weight: 400; color: #555; }
  .why-rule { width: 110px; height: 1px; background: #555; margin: 4px auto 0; }
  .why-intro { margin-top: 16px; font-size: 15px; line-height: 28px; color: var(--muted); }
  .benefits { position: absolute; top: 268px; left: 134px; display: flex; gap: 17px; }
  .benefit { width: 220px; height: 195px; background: var(--white); padding-top: 30px; }
  .benefit svg { display: block; margin: 0 auto; }
  .benefit h3 { font-size: 19px; font-weight: 400; color: #444; margin-top: 12px; }
  .benefit p { font-size: 12px; line-height: 18px; color: var(--muted); margin: 8px auto 0; width: 180px; }

  .feature { position: absolute; left: 0; width: 1200px; height: 325px; }
  .feature-photo { position: absolute; top: 0; width: 600px; height: 100%; }
  .feature-text { position: absolute; width: 440px; }
  .feature-text h2 { font-size: 30px; font-weight: 500; color: #444; }
  .feature-text p { font-size: 15px; line-height: 26px; color: var(--muted); margin-top: 16px; }
  .feature-strong { top: 1149px; }
  .feature-strong .feature-photo { left: 0; background: linear-gradient(135deg, #5a5a5a, #7d6a72 50%, #3b3b3b); }
  .feature-strong .feature-text { left: 646px; top: 84px; }
  .feature-clean { top: 1474px; }
  .feature-clean .feature-photo { left: 600px; background: linear-gradient(135deg, #e8e2d8, #c8b6a6 50%, #a88f86); }
  .feature-clean .feature-text { left: 133px; top: 84px; }
  .feature-water { top: 1799px; }
  .feature-water .feature-photo { left: 0; background: linear-gradient(135deg, #3a2518, #b4562a 40%, #4a3a30 70%, #2c2420); }
  .feature-water .feature-text { left: 646px; top: 84px; }

  .offer { position: absolute; top: 2124px; left: 0; width: 1200px; height: 217px; background: var(--cta-bg); }
  .offer-rate { position: absolute; left: 132px; top: 60px; font-size: 84px; font-weight: 500; color: var(--green); line-height: 1; }
  .offer-text { position: absolute; left: 353px; top: 76px; font-size: 25px; font-weight: 500; color: #444; line-height: 33px; }
  .offer-cta { position: absolute; left: 872px; top: 76px; width: 194px; height: 35px; }
  .offer-note { position: absolute; left: 872px; width: 194px; top: 124px; text-align: right; font-size: 12px; color: var(--muted); }
  .offer-edge { position: absolute; bottom: 0; left: 0; width: 1200px; height: 5px; background: var(--teal-line); }
</style>
</head>
<body>
  <header class="site-header">
    <div class="brand">
      <span class="brand-mark"></span>
      <span class="brand-name">Tuvelo<br>Basics i bambus</span>
    </div>
    <nav class="main-nav">
      <a class="active" style="left:0">Home</a>
      <a style="left:82px">Why Bamboo</a>
      <a style="left:212px">About us</a>
      <a style="left:316px">Reviews</a>
    </nav>
    <a class="btn header-cta">Buy now</a>
  </header>

  <section class="hero">
    <div class="hero-photo" role="img" aria-label="Photo of feet in cosy cream knitted bamboo socks resting on a soft blanket"></div>
    <div class="hero-shade"></div>
    <div class="hero-content">
      <h1 class="hero-title">Enjoy Your First Pair of Bamboo Socks for Only 20 DKK</h1>
      <ul class="hero-points">
        <li><svg width="16" height="12" viewBox="0 0 16 12"><path d="M1 6l5 5L15 1" fill="none" stroke="#fff" stroke-width="1.6"/></svg>We have been working on textile for more than 10 years</li>
        <li><svg width="16" height="12" viewBox="0 0 16 12"><path d="M1 6l5 5L15 1" fill="none" stroke="#fff" stroke-width="1.6"/></svg>All products meet our high quality standards</li>
        <li><svg width="16" height="12" viewBox="0 0 16 12"><path d="M1 6l5 5L15 1" fill="none" stroke="#fff" stroke-width="1.6"/></svg>Our customers loves us, and we have a 5 stars rating at scorevane.com</li>
      </ul>
      <div class="hero-actions">
        <a class="btn">Buy now</a>
        <a class="btn btn-outline"><svg width="11" height="13" viewBox="0 0 11 13"><path d="M0 0l11 6.5L0 13z" fill="#fff"/></svg>Watch video</a>
      </div>
      <p class="hero-note">Shipment included</p>
    </div>
  </section>

  <section class="why">
    <h2 class="why-title">Why Bamboo Clothing?</h2>
    <div class="why-rule"></div>
    <p class="why-intro">It was only in 2011 that the University of Nordhaven discovered how you can make fabric<br>from bamboo stems. Now bamboo has the potential to become the textile of the future.</p>
    <div class="benefits">
      <div class="benefit">
        <svg width="40" height="36" viewBox="0 0 40 36"><path d="M13 2l-11 6 4 8 5-2v20h18V14l5 2 4-8-11-6c-1 4-4 6-7 6s-6-2-7-6z" fill="none" stroke="#37b088" stroke-width="1.8" stroke-linejoin="round"/></svg>
        <h3>Comfortable</h3>
        <p>Bamboo fabric breathes making you comfortable in garments made in this.</p>
      </div>
      <div class="benefit">
        <svg width="38" height="36" viewBox="0 0 38 36"><circle cx="19" cy="18" r="15" fill="none" stroke="#37b088" stroke-width="1.8"/><path d="M11 25c2-9 8-14 16-14-1 9-7 14-16 14z" fill="none" stroke="#37b088" stroke-width="1.8"/></svg>
        <h3>Eco-friendly</h3>
        <p>Bamboo is a very fast-growing, tropical forest product, which does not require the use of pesticides</p>
      </div>
      <div class="benefit">
        <svg width="40" height="36" viewBox="0 0 40 36"><path d="M13 2l-11 6 4 8 5-2v20h18V14l5 2 4-8-11-6c-1 4-4 6-7 6s-6-2-7-6z" fill="none" stroke="#37b088" stroke-width="1.8" stroke-linejoin="round"/><path d="M15 20h10M15 25h10" stroke="#37b088" stroke-width="1.6"/></svg>
        <h3>Exquistely soft</h3>
        <p>The moment you wear it next to your skin you will notice the difference between other fabrics.</p>
      </div>
      <div class="benefit">
        <svg width="36" height="36" viewBox="0 0 36 36"><circle cx="18" cy="5" r="3" fill="none" stroke="#37b088" stroke-width="1.8"/><path d="M6 28c0-10 5-20 12-20s12 10 12 20z" fill="none" stroke="#37b088" stroke-width="1.8"/><rect x="4" y="28" width="28" height="6" fill="none" stroke="#37b088" stroke-width="1.8"/><path d="M9 18h18M8 23h20" stroke="#37b088" stroke-width="1.4"/></svg>
        <h3>Thermo-control</h3>
        <p>Bamboo fabric is warm, thanks to its hollow microfibre, yet is also breathable.</p>
      </div>
    </div>
  </section>

  <section class="feature feature-strong">
    <div class="feature-photo" role="img" aria-label="Photo of grey argyle bamboo socks lying on black leather dress shoes"></div>
    <div class="feature-text">
      <h2>Strong Material</h2>
      <p>Bamboo fabric is lightweight yet strong. The natural processing of verdanix bamboo allows the fibre to remain strong to produce an extremely high quality product. This process gives a material that is very durable.</p>
    </div>
  </section>

  <section class="feature feature-clean">
    <div class="feature-text">
      <h2>Completely Clean</h2>
      <p>Bamboo fibers doesnot under go much chemical processing to make the fabric ; so you can easily wear it without causing any allergic irritation to the skin that is more prevalent with heavily processes fabrics.</p>
    </div>
    <div class="feature-photo" role="img" aria-label="Photo of a family relaxing on a sofa with their feet up in striped and patterned socks"></div>
  </section>

  <section class="feature feature-water">
    <div class="feature-photo" role="img" aria-label="Photo of feet in patterned wool socks warming in front of a fireplace"></div>
    <div class="feature-text">
      <h2>Water Absorbent</h2>
      <p>Bamboo fibers are water absobent. So if you live in a humid environment this is the fabric for you. Think of the sweat it will absorb and evaporate out of your body.</p>
    </div>
  </section>

  <section class="offer">
    <div class="offer-rate">-90%</div>
    <p class="offer-text">Get Your First Pair of Socks With<br>an Exclusive Discount</p>
    <a class="btn offer-cta">Buy now</a>
    <p class="offer-note">Shipment included</p>
    <div class="offer-edge"></div>
  </section>
</body>
</html>
```